Book Cover Design for Millennial

I need a book cover design for my book Quiet Summit. The subtitle of the book is Steps for Building a Life You Savor at the Office.

I'm a career coach who helps millennial career professionals. I myself am a millennial but on the older end (34). I've dealt and been through most of the challenges millennials are facing as career professionals and I wrote this book with the thought of providing guidance and aid to getting past those challenges and shedding light on fundamental habits and practices that will help them excel in their careers. In addition, the book will help them prepare millennials for our turn as the leaders, managers, etc moving forward in corporate America. The final design should have the main title of the book in it as the focal point but not the subtitle. I want the cover to communicate something NEW, Bold, Youthful, non-traditional. I want it to stick out while still maintaining a sleek and Professional look.
Updates

Hello, Designers! I want to thank you all for your submissions! The work is amazing and I greatly appreciate it. If you would I want to help out in this process by adding a few updates based on the submissions I have seen. The concept I think that is coming close to hitting the mark is Corvo Graphix. What I would like to see changed about the concept is the following: Change the outfits to be more Millennial Career Professional. I have attached some ideas to the brief. I want to replace this picture with one of multiple millennials anywhere from 3 and up. I would like the pic to have diversity in it representing most races of people in the USA. I would like my name beneath quiet summit. I'm not a known author yet so having my name that big my distract from the title of the book. Can we make the title a little bigger and so far I like the background.Thanks, DR Added Friday, September 30, 2016

Target Market(s)

Millennial Career Professionals (18 - 34 age group)

Industry/Entity Type

Life Coaching

Logo Text

Quiet Summit

Requirements
Must have
• communicate something NEW, Bold, Youthful, non-traditional. I want it to stick out while still maintaining a sleek and Professional look.
Nice to have
• something that goes with my brand
• http://www.dariusrenfield.example
Should not have
• Nothing 3D or a logo that is hard to read when placed on stationeries, business cards etc

```html
<!DOCTYPE html>
<html lang="en">
<head>
<meta charset="utf-8">
<title>Quiet Summit – Book Cover</title>
<link href="https://fonts.googleapis.com/css2?family=Oswald:wght@500;600&family=Noto+Serif:wght@400&display=swap" rel="stylesheet">
<style>
  :root {
    --page-bg: #ffffff;
    --cover-black: #050505;
    --glow-grey: #8a8a8a;
    --title-yellow: #f7c91c;
    --title-yellow-light: #f9e23d;
    --band-yellow: #f5c61a;
    --band-yellow-light: #f8e03a;
    --subtitle-white: #f4f4f4;
    --rule-grey: #9a9a9a;
    --ink-black: #111111;
  }
  * { box-sizing: border-box; margin: 0; padding: 0; }
  html, body {
    width: 1200px;
    height: 1135px;
    overflow: hidden;
    background: var(--page-bg);
  }
  .canvas {
    position: relative;
    width: 1200px;
    height: 1135px;
  }
  .cover {
    position: absolute;
    left: 252px;
    top: 18px;
    width: 696px;
    height: 1100px;
    background: var(--cover-black);
    overflow: hidden;
    box-shadow: 0 6px 24px rgba(0,0,0,0.25);
  }
  .cover-glow {
    position: absolute;
    inset: 0 0 auto 0;
    height: 620px;
    background: radial-gradient(ellipse 70% 75% at 50% 0%, var(--glow-grey) 0%, #3a3a3a 45%, var(--cover-black) 85%);
  }
  .team-photo {
    position: absolute;
    left: 70px;
    top: 75px;
    width: 556px;
    height: 450px;
    border-radius: 40px 40px 0 0;
    background: linear-gradient(180deg, rgba(110,100,90,0.85) 0%, rgba(70,65,62,0.8) 45%, rgba(20,20,20,0.2) 100%);
  }
  .title {
    position: absolute;
    left: 0;
    right: 0;
    top: 500px;
    text-align: center;
    font-family: "Oswald", sans-serif;
    font-weight: 600;
    font-size: 178px;
    line-height: 160px;
    letter-spacing: 1px;
    text-transform: uppercase;
    background: linear-gradient(90deg, var(--title-yellow) 0%, var(--title-yellow-light) 50%, var(--title-yellow) 100%);
    -webkit-background-clip: text;
    background-clip: text;
    color: transparent;
  }
  .subtitle-block {
    position: absolute;
    left: 118px;
    right: 118px;
    top: 868px;
  }
  .subtitle-rule {
    height: 1px;
    background: linear-gradient(90deg, transparent, var(--rule-grey), transparent);
  }
  .subtitle {
    padding: 6px 0 10px;
    text-align: center;
    font-family: "Noto Serif", serif;
    font-size: 36px;
    line-height: 44px;
    color: var(--subtitle-white);
  }
  .author-band {
    position: absolute;
    left: 0;
    right: 0;
    bottom: 0;
    height: 128px;
    background: linear-gradient(90deg, var(--band-yellow) 0%, var(--band-yellow-light) 55%, var(--band-yellow) 100%);
    display: flex;
    align-items: center;
    justify-content: center;
  }
  .author-name {
    font-family: "Oswald", sans-serif;
    font-weight: 500;
    font-size: 46px;
    letter-spacing: 12px;
    color: var(--ink-black);
    text-transform: uppercase;
  }
</style>
</head>
<body>
<div class="canvas">
  <section class="cover">
    <div class="cover-glow"></div>
    <div class="team-photo" role="img" aria-label="Photo of a diverse group of young professionals in suits standing with arms crossed"></div>
    <h1 class="title">Quiet<br>Summit</h1>
    <div class="subtitle-block">
      <div class="subtitle-rule"></div>
      <p class="subtitle">Steps for Building a Life<br>You Savor at the Office</p>
      <div class="subtitle-rule"></div>
    </div>
    <div class="author-band">
      <span class="author-name">Author Name</span>
    </div>
  </section>
</div>
</body>
</html>
```